Web Design job - NetKestrel Company including Desktop & Mobile version

Create a Web Design (Uncoded - PSD layout only)

1. About our company

NetKestrel is an Australian-based company which sells used networking devices to coporates and other brokers in USA, Europe and other countries. We are the market leader in this space and currently have warehouses in Sydney and California. Most of our products are from VORLAN.

Our competitive advantages come from lowest price in the market, flexible product configuration for different demands of customers, long time experience in the business and huge stock of inventory.

We are in need of a new website to enhance customer and partner engagement which are measured by sales metrics and website performance metrics such as number of request for a quote, number of new orders, return visits, views, conversion rate, etc.

2. Website structure:

We need different looks for different devices: Desktop, iPad and Mobile with popular screen resolutions for each of following page.

Try to make one as good as possible, then we can move further. Below are the main pages of the web:

+ Home Page: Where customers learn about the company and its business. Should have: Beautiful company profile, highlighted company contact and strengths; A comprehensive overview about selling products.

+ Category Page: Where customers learn about products in a category and do the search action. Should focus on filter and sort functions for easily finding a product.

+ Product Page: Where customers learn about the details of a specific products such as price, image, description, related products.
- Also need features for cross-sell or up-sell.
- An item may have both new and refurbished prices, or either or none of them. Should have options to choose between new or refurbished price to add to cart.

+ Information Page: About the company, Company Announcement.

+ Cart management and Check-out

+ Search results

REFERENCES
Current website: http://netkestrel.com.au/

Prefered Layout:
- https://www.gearbazaar-example.com/en/vorlan-systems/vorlan-router-series/vorlan-series-1900/vorlan-systems-vorlan1941-k9
- https://www.wiresandboxes-example.com/vorlan-2port-rj48-multiflex-t1-trunk-card-vwic2mftt1-p-1374.html
- The attached files play as wireframes, only for the purpose of guiding. You are free to make your choices of colors and layouts.

Target Market(s)

- Corporate clients
- Main market: Australia

Industry/Entity Type

It Company

Number of Pages Required

3 page

Font styles to use
Sans Serif

Requirements
Must have
• - The new design should have a clear look to easily find information while should look professional to aim at corporate clients.
• - Require least time or effort to finish a task
• - Optimize for SEO and loading time
• - Mobile version is optimized for touching, swiping and loading time.
• - Bear in mind that the new website need minimum effort of manual tasks such as updating content. We don’t have human resources for these yet.
Nice to have
• - Should have design for each scenario such as click, popup, dropdown, deactive, have/not have an object

```html
<!DOCTYPE html>
<html lang="en">
<head>
<meta charset="utf-8">
<title>NetKestrel – Networking Equipment</title>
<link href="https://fonts.googleapis.com/css2?family=Open+Sans:ital,wght@0,400;0,600;0,700;0,800;1,700&display=swap" rel="stylesheet">
<style>
:root{
  --blue:#1677c8;
  --orange:#e84e1b;
  --navy:#2b2170;
  --yellow:#f5e61b;
  --ink:#222;
  --muted:#777;
  --grey-bg:#e9e9e9;
  --card-line:#dcdcdc;
  --dark:#1f1f1f;
  --darker:#181818;
  --white:#fff;
}
*{box-sizing:border-box;margin:0;padding:0}
html,body{width:1200px;height:3871px;overflow:hidden}
body{font-family:"Open Sans",Arial,sans-serif;color:var(--ink);background:var(--white);position:relative}
.abs{position:absolute}
section,header,nav,footer{position:absolute;left:0;width:1200px}

/* header */
.site-header{top:0;height:126px;background:var(--white)}
.brand{left:134px;top:40px;display:flex;align-items:center;gap:10px}
.brand-dot{width:48px;height:48px;border-radius:50%;background:var(--orange)}
.brand-name{font-size:30px;font-weight:700;color:var(--blue);letter-spacing:-.5px}
.top-contact{right:134px;top:14px;font-size:13px;color:var(--blue);display:flex;gap:10px;align-items:center}
.top-contact .sep{color:#bbb}
.search{left:395px;top:57px;width:353px;height:42px;border:2px solid var(--blue);display:flex}
.search span{flex:1;font-size:10px;color:#888;padding:13px 12px;letter-spacing:.3px}
.search .btn{width:42px;background:var(--blue);display:flex;align-items:center;justify-content:center}
.cart{left:774px;top:57px;width:134px;height:42px;border:1px solid #ccc;display:flex;align-items:center;justify-content:center;gap:8px;font-size:11px;font-weight:600;color:#555}
.quote-btn{left:926px;top:57px;width:140px;height:42px;background:var(--orange);color:var(--white);font-size:11px;font-weight:700;display:flex;align-items:center;justify-content:center}

.main-nav{top:126px;height:34px;background:var(--blue)}
.main-nav a{position:absolute;top:10px;font-size:11px;font-weight:700;color:var(--white);text-decoration:none}

/* hero */
.hero{top:160px;height:568px;background:var(--grey-bg)}
.hero-rack{left:90px;top:278px;width:413px;height:104px;border-radius:6px;background:linear-gradient(#3a3a3a,#111)}
.hero-router{left:555px;top:8px;width:542px;height:464px;border-radius:24px;background:linear-gradient(180deg,#dfe6ec 0%,#f4f6f8 40%,#c9cfd4 100%)}
.promo{left:134px;top:72px;width:349px;height:238px;background:var(--orange);color:var(--white);text-align:center}
.promo h2{margin-top:28px;font-size:31px;font-weight:800}
.promo p{font-size:12px;font-weight:700;font-style:italic;margin-top:4px}
.promo .stock{position:absolute;left:52px;top:116px;width:253px;height:50px;background:var(--yellow);color:var(--orange);font-weight:800;font-size:17px;display:flex;align-items:center;justify-content:center}
.dots{left:568px;top:529px;display:flex;gap:8px}
.dots i{width:7px;height:7px;border-radius:50%;background:#bbb;display:block}
.dots i.on{background:var(--orange)}

/* sections */
.section-title{width:1200px;text-align:center;font-size:22px;font-weight:700;color:var(--orange)}
.categories{top:728px;height:524px;background:var(--white)}
.card{background:var(--white);text-align:center}
.cat-card{top:129px;height:322px;border:4px solid #e2e2e2}
.img-ph{position:absolute;left:50%;transform:translateX(-50%);border-radius:4px}
.card .name{position:absolute;width:100%;font-size:12px;font-weight:600;color:var(--ink)}
.card .price{position:absolute;width:100%;font-size:16px;font-weight:700}
.card .price s{font-size:12px;font-weight:400;color:#888;margin-right:6px}
.shop{position:absolute;left:50%;transform:translateX(-50%);width:100px;height:28px;background:var(--orange);color:var(--white);font-size:10px;font-weight:700;display:flex;align-items:center;justify-content:center}

.products{height:508px;background:var(--grey-bg)}
.prod-card{top:139px;height:291px;box-shadow:0 1px 3px rgba(0,0,0,.08)}

.welcome{top:1760px;height:529px;background:var(--white)}
.welcome .lead{left:300px;top:118px;width:600px;text-align:center;font-size:12.5px;line-height:1.55;color:#444}
.stat{top:240px;height:206px;background:var(--blue);color:var(--white);text-align:center}
.stat svg{margin-top:34px}
.stat .num{font-size:36px;font-weight:700;margin-top:10px}
.stat .lbl{font-size:11px;font-weight:600;margin-top:14px;line-height:1.5}

.request{top:2795px;height:495px;background:var(--white)}
.request h3{left:199px;top:95px;font-size:24px;font-weight:700;color:var(--orange)}
.circle{width:58px;height:58px;border-radius:50%;background:var(--blue);display:flex;align-items:center;justify-content:center}
.req-phone{left:279px;top:180px;font-size:29px;font-weight:700}
.req-sub{left:279px;top:228px;font-size:15px;line-height:1.6;color:#444}
.req-or{left:279px;top:325px;font-size:15px;color:#444}
.req-mail{left:279px;top:354px;font-size:22px;font-weight:700}
.agent{left:684px;top:30px;width:426px;height:465px;background:linear-gradient(180deg,#f6f3f0 0%,#ece6e0 55%,#dcd6d2 100%);border-radius:200px 200px 0 0}

.bands{top:3290px;height:90px}
.band{top:0;height:90px;color:var(--white);display:flex;align-items:center;justify-content:center;gap:18px;font-size:17px;font-weight:700}

.features{top:3380px;height:78px;background:var(--dark);color:var(--white)}
.feat{top:30px;font-size:12px;display:flex;align-items:center;gap:8px}

.site-footer{top:3458px;height:413px;background:var(--darker);color:#999}
.site-footer h4{top:64px;font-size:12px;font-weight:700;color:var(--white)}
.about-text{left:134px;top:106px;width:250px;font-size:10.5px;line-height:1.6;color:#6d6d6d}
.contact-list{left:483px;top:100px;list-style:none;font-size:10.5px;color:#777}
.contact-list li{display:flex;align-items:center;gap:12px;height:24px}
.contact-list i{width:8px;height:8px;border-radius:50%;background:#555;display:block}
.pay{top:118px;width:50px;height:32px;border-radius:3px;background:#f1f1f1}
.foot-brand{left:134px;top:310px;display:flex;align-items:center;gap:10px}
.foot-brand .brand-name{font-size:30px}
.copyright{right:111px;top:333px;font-size:11px;color:#666}
</style>
</head>
<body>

<header class="site-header">
  <div class="abs brand"><span class="brand-dot"></span><span class="brand-name">NetKestrel</span></div>
  <div class="abs top-contact">
    <svg width="12" height="12" viewBox="0 0 24 24"><path fill="#e84e1b" d="M6.6 10.8a15 15 0 006.6 6.6l2.2-2.2c.3-.3.7-.4 1-.2 1.1.4 2.3.6 3.6.6.6 0 1 .4 1 1V20c0 .6-.4 1-1 1A17 17 0 013 4c0-.6.4-1 1-1h3.5c.6 0 1 .4 1 1 0 1.3.2 2.5.6 3.6.1.3 0 .7-.2 1z"/></svg>
    <span>(+61) 02 9555 0142</span><span class="sep">|</span>
    <svg width="12" height="10" viewBox="0 0 24 18"><rect width="24" height="18" rx="2" fill="#1677c8"/><path d="M2 2l10 8 10-8" stroke="#fff" stroke-width="2" fill="none"/></svg>
    <span>sales@netkestrel.com.au</span>
  </div>
  <div class="abs search"><span>SEARCH WITH PRODUCT NAME</span><div class="btn">
    <svg width="16" height="16" viewBox="0 0 24 24"><circle cx="10" cy="10" r="7" stroke="#fff" stroke-width="3" fill="none"/><path d="M15 15l6 6" stroke="#fff" stroke-width="3"/></svg></div></div>
  <div class="abs cart">
    <svg width="16" height="14" viewBox="0 0 24 20"><path d="M1 1h4l3 12h12l3-9H6" stroke="#666" stroke-width="2" fill="none"/><circle cx="9" cy="17" r="2" fill="#666"/><circle cx="19" cy="17" r="2" fill="#666"/></svg>
    MY CART (0)</div>
  <div class="abs quote-btn">REQUEST A QUOTE</div>
</header>

<nav class="main-nav">
  <a style="left:134px">HOME</a><a style="left:212px">ROUTERS</a><a style="left:310px">SWITCHES</a>
  <a style="left:408px">WIRELESSES</a><a style="left:524px">IP PHONES</a><a style="left:630px">ACCESSORIES</a>
</nav>

<section class="hero">
  <div class="abs hero-rack" role="img" aria-label="Rack-mounted network switch"></div>
  <div class="abs hero-router" role="img" aria-label="White wireless router with blue antennas"></div>
  <div class="abs promo">
    <h2>SAVE UP TO 40%</h2>
    <p>BY DOING BUSINESS WITH NETKESTREL</p>
    <div class="stock">STOCK LIST &nbsp;»</div>
  </div>
  <div class="abs dots"><i></i><i class="on"></i><i></i><i></i><i></i></div>
</section>

<section class="categories">
  <div class="abs section-title" style="top:44px">PRODUCT CATEGORIES</div>
  <div class="abs card cat-card" style="left:134px;width:294px">
    <div class="img-ph" role="img" aria-label="Wireless router" style="top:16px;width:200px;height:136px;background:linear-gradient(#4a5d78,#253043)"></div>
    <div class="name" style="top:201px">WIRELESS &amp; ROUTERS</div>
    <div class="price" style="top:222px"><s>$45.99</s>$35.99</div>
    <div class="shop" style="top:266px">SHOP NOW</div>
  </div>
  <div class="abs card cat-card" style="left:454px;width:284px">
    <div class="img-ph" role="img" aria-label="Network switch" style="top:60px;width:210px;height:50px;background:linear-gradient(#5a6878,#2e3945)"></div>
    <div class="name" style="top:201px">SWITCHES</div>
    <div class="price" style="top:222px"><s>$45.99</s>$35.99</div>
    <div class="shop" style="top:266px">SHOP NOW</div>
  </div>
  <div class="abs card cat-card" style="left:766px;width:297px">
    <div class="img-ph" role="img" aria-label="Desk IP phone" style="top:16px;width:150px;height:136px;background:linear-gradient(#6b6f74,#2d2f33)"></div>
    <div class="name" style="top:201px">IP PHONES</div>
    <div class="price" style="top:222px"><s>$45.99</s>$35.99</div>
    <div class="shop" style="top:266px">SHOP NOW</div>
  </div>
</section>

<section class="products" style="top:1252px">
  <div class="abs section-title" style="top:56px">NEW PRODUCTS</div>
  <svg class="abs" style="left:56px;top:250px" width="14" height="26" viewBox="0 0 14 26"><path d="M12 2L2 13l10 11" stroke="#888" stroke-width="2.5" fill="none"/></svg>
  <svg class="abs" style="left:1116px;top:250px" width="14" height="26" viewBox="0 0 14 26"><path d="M2 2l10 11L2 24" stroke="#888" stroke-width="2.5" fill="none"/></svg>
  <div class="abs card prod-card" style="left:134px;width:214px">
    <div class="img-ph" role="img" aria-label="Green voice module card" style="top:22px;width:170px;height:74px;background:linear-gradient(#3e7a3a,#1f4a22)"></div>
    <div class="name" style="top:150px;font-size:11px">NK-VM80 REFURBISHED</div>
    <div class="price" style="top:172px"><s>$245.99</s>$230</div>
    <div class="shop" style="top:232px">SHOP NOW</div>
  </div>
  <div class="abs card prod-card" style="left:366px;width:214px">
    <div class="img-ph" role="img" aria-label="24-port switch" style="top:40px;width:180px;height:38px;background:linear-gradient(#60656b,#33373c)"></div>
    <div class="name" style="top:150px;font-size:11px">NK-SW740 REFURBISHED</div>
    <div class="price" style="top:172px"><s>$245.99</s>$345</div>
    <div class="shop" style="top:232px">SHOP NOW</div>
  </div>
  <div class="abs card prod-card" style="left:601px;width:219px">
    <div class="img-ph" role="img" aria-label="Green memory module" style="top:22px;width:120px;height:90px;background:linear-gradient(135deg,#4a8a3c,#1f5020)"></div>
    <div class="name" style="top:150px;font-size:11px">NK-VM20 REFURBISHED</div>
    <div class="price" style="top:172px"><s>$245.99</s>$345</div>
    <div class="shop" style="top:232px">SHOP NOW</div>
  </div>
  <div class="abs card prod-card" style="left:841px;width:222px">
    <div class="img-ph" role="img" aria-label="Network interface board" style="top:18px;width:170px;height:100px;background:linear-gradient(135deg,#4f6f4a,#1e2c1c)"></div>
    <div class="name" style="top:150px;font-size:11px">NK-AP515 REFURBISHED</div>
    <div class="price" style="top:172px"><s>$245.99</s>$500</div>
    <div class="shop" style="top:232px">SHOP NOW</div>
  </div>
</section>

<section class="welcome">
  <div class="abs section-title" style="top:64px">WELCOME TO NETKESTREL</div>
  <p class="abs lead">With over fifteen years experience selling and buying new and used networking equipment, NetKestrel is one of the most preeminent and longest established businesses in the global reseller marketplace. The manufacturers that we specialise in include: Vorlan, Tarnline (New Products Only), Orvix, Calvane, Brellis, Quadnet, Castwell, Meridyn, Loomfield and Parcelon.</p>
  <div class="abs stat" style="left:134px;width:222px">
    <svg width="26" height="24" viewBox="0 0 26 24"><rect x="1" y="6" width="24" height="17" rx="2" fill="#fff"/><rect x="8" y="1" width="10" height="7" rx="1" stroke="#fff" stroke-width="2" fill="none"/></svg>
    <div class="num">7</div><div class="lbl">YEARS OF EXPERIENCE</div></div>
  <div class="abs stat" style="left:372px;width:222px">
    <svg width="26" height="24" viewBox="0 0 26 24"><rect x="1" y="4" width="19" height="19" rx="2" stroke="#fff" stroke-width="2" fill="none"/><path d="M10 15l2-5 10-9 3 3-10 9z" fill="#fff"/></svg>
    <div class="num">99.5%</div><div class="lbl">POSITIVE FEEDBACK<br>ON TRADEHUB</div></div>
  <div class="abs stat" style="left:609px;width:222px">
    <svg width="30" height="24" viewBox="0 0 30 24"><circle cx="15" cy="7" r="5" fill="#fff"/><path d="M5 23c0-6 4-9 10-9s10 3 10 9z" fill="#fff"/><circle cx="5" cy="9" r="3" fill="#fff"/><circle cx="25" cy="9" r="3" fill="#fff"/></svg>
    <div class="num">300</div><div class="lbl">CLIENTS &amp; PARTNERS<br>AROUND THE WORLD</div></div>
  <div class="abs stat" style="left:846px;width:220px">
    <svg width="26" height="24" viewBox="0 0 26 24"><path d="M13 2l11 6-11 6L2 8z" fill="#fff"/><path d="M2 12l11 6 11-6v4l-11 6-11-6z" fill="#fff"/></svg>
    <div class="num">1.250</div><div class="lbl">SKUs &nbsp;IN INVENTORY</div></div>
</section>

<section class="products" style="top:2289px">
  <div class="abs section-title" style="top:58px">POPULAR PRODUCTS</div>
  <svg class="abs" style="left:56px;top:250px" width="14" height="26" viewBox="0 0 14 26"><path d="M12 2L2 13l10 11" stroke="#888" stroke-width="2.5" fill="none"/></svg>
  <svg class="abs" style="left:1116px;top:250px" width="14" height="26" viewBox="0 0 14 26"><path d="M2 2l10 11L2 24" stroke="#888" stroke-width="2.5" fill="none"/></svg>
  <div class="abs card prod-card" style="left:134px;width:214px">
    <div class="img-ph" role="img" aria-label="Stackable switch" style="top:62px;width:170px;height:34px;background:linear-gradient(#4d7a8c,#254452)"></div>
    <div class="name" style="top:150px;font-size:11px">VORLAN KX SERIES</div>
    <div class="price" style="top:172px"><s>$245.99</s>$230</div>
    <div class="shop" style="top:232px">SHOP NOW</div>
  </div>
  <div class="abs card prod-card" style="left:366px;width:214px">
    <div class="img-ph" role="img" aria-label="Voice interface card" style="top:30px;width:120px;height:86px;background:linear-gradient(135deg,#8a8f95,#3b4046)"></div>
    <div class="name" style="top:150px;font-size:11px">NK-VC330 REFURBISHED</div>
    <div class="price" style="top:172px"><s>$245.99</s>$345</div>
    <div class="shop" style="top:232px">SHOP NOW</div>
  </div>
  <div class="abs card prod-card" style="left:601px;width:219px">
    <div class="img-ph" role="img" aria-label="Boxed trunk card" style="top:30px;width:110px;height:80px;background:linear-gradient(135deg,#c8a57a,#8c6a44)"></div>
    <div class="name" style="top:150px;font-size:11px">NK-TR618 BRAND NEW</div>
    <div class="price" style="top:172px"><s>$245.99</s>$345</div>
    <div class="shop" style="top:232px">SHOP NOW</div>
  </div>
  <div class="abs card prod-card" style="left:841px;width:222px">
    <div class="img-ph" role="img" aria-label="Network interface board" style="top:34px;width:120px;height:80px;background:linear-gradient(135deg,#4f7a4a,#1e3a1c)"></div>
    <div class="name" style="top:150px;font-size:11px">NK-AP515 REFURBISHED</div>
    <div class="price" style="top:172px"><s>$245.99</s>$500</div>
    <div class="shop" style="top:232px">SHOP NOW</div>
  </div>
</section>

<section class="request">
  <h3 class="abs">REQUEST A QUOTE</h3>
  <div class="abs circle" style="left:191px;top:176px">
    <svg width="24" height="24" viewBox="0 0 24 24"><path fill="#fff" d="M6.6 10.8a15 15 0 006.6 6.6l2.2-2.2c.3-.3.7-.4 1-.2 1.1.4 2.3.6 3.6.6.6 0 1 .4 1 1V20c0 .6-.4 1-1 1A17 17 0 013 4c0-.6.4-1 1-1h3.5c.6 0 1 .4 1 1 0 1.3.2 2.5.6 3.6.1.3 0 .7-.2 1z"/></svg></div>
  <div class="abs req-phone">(061) 02 9555 0142</div>
  <p class="abs req-sub">Call today for a great -price on new and<br>used networking equipment</p>
  <div class="abs circle" style="left:191px;top:324px">
    <svg width="24" height="18" viewBox="0 0 24 18"><rect width="24" height="18" rx="2" fill="#fff"/><path d="M2 2l10 8 10-8" stroke="#1677c8" stroke-width="2" fill="none"/></svg></div>
  <div class="abs req-or">Or email to</div>
  <div class="abs req-mail">sales@netkestrel.com.au</div>
  <div class="abs agent" role="img" aria-label="Customer service agent with headset"></div>
</section>

<section class="bands">
  <div class="abs band" style="left:0;width:395px;background:var(--blue)">
    <svg width="38" height="38" viewBox="0 0 38 38"><circle cx="19" cy="19" r="17" stroke="#fff" stroke-width="2.5" fill="none"/><path d="M19 9l8 3v6c0 5-4 9-8 10-4-1-8-5-8-10v-6z" fill="#fff"/></svg>WARRANTY</div>
  <div class="abs band" style="left:395px;width:392px;background:var(--orange)">
    <svg width="28" height="36" viewBox="0 0 28 36"><path d="M7 15V10a7 7 0 0114 0v5" stroke="#fff" stroke-width="3" fill="none"/><rect x="2" y="15" width="24" height="19" rx="2" fill="#fff"/></svg>PRIVACY STATEMENT</div>
  <div class="abs band" style="left:787px;width:413px;background:var(--navy)">
    <svg width="30" height="36" viewBox="0 0 30 36"><rect x="2" y="2" width="26" height="32" rx="2" fill="#fff"/><path d="M8 11h14M8 17h14M8 23h10" stroke="#2b2170" stroke-width="2.5"/></svg>TERMS OF TRADE</div>
</section>

<section class="features">
  <div class="abs feat" style="left:134px"><b style="font-size:15px">$</b>100% Wholesale Price</div>
  <div class="abs feat" style="left:302px"><svg width="14" height="14" viewBox="0 0 24 24"><path fill="#fff" d="M2 10h4v12H2zM8 22h10c1 0 2-1 2-2l2-8c0-1-1-2-2-2h-6l1-5c0-2-3-3-4-1L8 10z"/></svg>100% Quality Assurance</div>
  <div class="abs feat" style="left:568px"><svg width="14" height="14" viewBox="0 0 24 24"><path d="M4 14v-2a8 8 0 0116 0v2" stroke="#fff" stroke-width="2.5" fill="none"/><rect x="2" y="13" width="5" height="8" rx="1" fill="#fff"/><rect x="17" y="13" width="5" height="8" rx="1" fill="#fff"/></svg>Free Support</div>
  <div class="abs feat" style="left:728px"><svg width="14" height="14" viewBox="0 0 24 24"><circle cx="12" cy="12" r="10" fill="#fff"/><path d="M7 12l3 3 7-7" stroke="#1f1f1f" stroke-width="2.5" fill="none"/></svg>100% Money Back Guarantee</div>
  <div class="abs feat" style="left:940px"><svg width="16" height="12" viewBox="0 0 24 18"><rect width="24" height="18" rx="2" fill="#fff"/><rect y="4" width="24" height="3" fill="#1f1f1f"/></svg>Flexible Payment</div>
</section>

<footer class="site-footer">
  <h4 class="abs" style="left:134px">ABOUT US</h4>
  <h4 class="abs" style="left:483px">CONTACT US</h4>
  <h4 class="abs" style="left:885px">PAYMENT</h4>
  <p class="abs about-text">We source tested networking gear for businesses of every size. Each item is checked, cleaned and graded by our team before it ships, so you get dependable hardware at a fair price. Our staff are happy to help you pick the right parts for your network and to answer questions about stock, delivery and warranty terms.</p>
  <ul class="abs contact-list">
    <li><i></i>Unit 12 / 48 Harbour Rd &nbsp;|&nbsp; Granville NSW 2142</li>
    <li><i></i>+61 2 9555 0142 &nbsp;|&nbsp; 04 5550 1187</li>
    <li><i></i>8:30 am – 5:30 pm / Mon – Fri (AEST)</li>
    <li><i></i>sales@netkestrel.com.au</li>
    <li><i></i>http://netkestrel.com.au/</li>
  </ul>
  <div class="abs pay" role="img" aria-label="Payment method badge" style="left:885px"></div>
  <div class="abs pay" role="img" aria-label="Payment method badge" style="left:946px"></div>
  <div class="abs pay" role="img" aria-label="Payment method badge" style="left:1008px"></div>
  <div class="abs foot-brand"><span class="brand-dot"></span><span class="brand-name">NetKestrel</span></div>
  <div class="abs copyright">Copyright @ 2017 All Rights Reserved.</div>
</footer>

</body>
</html>
```